Modern Label for cleaning products for the brand Vorlix

We need a label design for our line of cleaning products. The label should feature our logo and an image to identify the product's intended use. I've added our logo and an image for use. This only concerns the design of the label on the front of the bottle.

Label dimensions:
Label 1 (500ml bottle with spray): width 58mm x height 115mm
Label 2: (1L bottle): width 73mm x height 140mm
The design must be consistent for both bottles which you find in the pictures.

The bottles to be labeled are white. See the attachment for a photo of the bottles.

The photo must also appear on the label to identify the product's intended use.

Product information:
Brand: Vorlix
Product: Sanitary Cleaner

This text must be placed on the label:
"Cleans, descales & freshens. followed with this text: "Ideal for quick and powerful cleaning. A ready-to-use product for everyday use."

- Mention the seperate USP's: Sanitary, Bathroom, Toilet, Wet areas

Appearance: This is a consumer product, but it must have a professional appearance. We would like to see a design that use the color blue from our logo.

Target Market(s)

Consumers who take care of their homes and want to maintain it the correct (professional) way

Font styles to use
Sans Serif

Colors
0054AA
0677BA
7BADD7
CADEEF
E8F1F8

Requirements
Must have
• USP's + use of image and logo + blend in 1 design
Nice to have
• Keep the color of the logo in the design
Should not have
• Comic sans

```html
<!DOCTYPE html>
<html lang="en">
<head>
<meta charset="utf-8">
<title>Vorlix Sanitary Cleaner Label</title>
<link rel="stylesheet" href="https://fonts.googleapis.com/css2?family=Montserrat:ital,wght@0,400;0,500;0,600;0,700;0,800;1,700&display=swap">
<style>
  :root {
    --brand-deep: #0054AA;
    --brand-mid: #0677BA;
    --brand-soft: #7BADD7;
    --brand-pale: #CADEEF;
    --brand-mist: #E8F1F8;
    --accent-yellow: #FFF200;
    --ink: #2a2a2a;
    --heading-blue: #1a5f95;
    --white: #ffffff;
  }
  * { margin: 0; padding: 0; box-sizing: border-box; }
  html, body {
    width: 1200px; height: 898px; overflow: hidden;
    background: var(--white);
    font-family: "Montserrat", Arial, sans-serif;
  }
  .label {
    position: absolute; left: 424px; top: 100px;
    width: 358px; height: 703px;
    border-radius: 10px; overflow: hidden;
    box-shadow: 0 0 4px rgba(0,0,0,0.15);
  }
  .label-art { position: absolute; inset: 0; }
  .label > p, .label > div:not(.label-art) { position: absolute; }
  .tagline-small {
    top: 20px; width: 100%; text-align: center;
    font-size: 12px; font-weight: 400; color: var(--white); letter-spacing: 0.3px;
  }
  .tagline-main {
    top: 35px; width: 100%; text-align: center;
    font-size: 17px; font-weight: 500; color: var(--accent-yellow); letter-spacing: 0.4px;
  }
  .brand-mark {
    left: 163px; top: 92px; width: 42px; height: 42px;
    border-radius: 50%; background: var(--brand-mid);
  }
  .brand-name {
    top: 160px; width: 100%; text-align: center;
    font-size: 34px; font-weight: 700; color: var(--ink); letter-spacing: -0.5px;
  }
  .product-line {
    top: 223px; width: 100%; text-align: center; padding-right: 4px;
    font-size: 15px; font-weight: 700; color: var(--heading-blue); letter-spacing: 1px;
  }
  .product-name {
    top: 240px; width: 100%; text-align: center;
    font-size: 40px; font-weight: 400; color: var(--white); letter-spacing: 3px;
  }
  .claim-badge {
    left: 30px; top: 515px; width: 100px; text-align: center;
    font-size: 11px; font-weight: 800; line-height: 13px; color: #111; letter-spacing: 0.5px;
  }
  .usage-heading {
    left: 174px; top: 551px;
    font-size: 14px; font-weight: 700; color: var(--accent-yellow); letter-spacing: 1px;
  }
  .usage-list {
    list-style: none; position: absolute; top: 574px; left: 0;
    font-size: 13px; font-weight: 500; color: var(--white); letter-spacing: 1.2px; line-height: 16.3px;
  }
  .usage-list li::before {
    content: ""; display: inline-block; width: 6px; height: 6px; border-radius: 50%;
    background: var(--accent-yellow); margin-right: 6px; vertical-align: 2px;
  }
  .usage-list li:nth-child(1) { margin-left: 177px; }
  .usage-list li:nth-child(2) { margin-left: 183px; }
  .usage-list li:nth-child(3) { margin-left: 191px; }
  .usage-list li:nth-child(4) { margin-left: 197px; }
  .benefit-intro {
    left: 0; width: 256px; top: 653px; text-align: center;
    font-size: 10px; font-weight: 400; color: var(--white);
  }
  .benefit-main {
    left: 23px; top: 667px;
    font-size: 11px; font-weight: 700; font-style: italic; color: var(--ink); letter-spacing: 0.8px;
  }
  .volume {
    left: 264px; top: 648px;
    font-size: 31px; font-weight: 500; color: var(--white); letter-spacing: -1px;
  }
  .volume small { font-size: 16px; font-weight: 700; letter-spacing: 0; }
  .volume-unit {
    left: 276px; top: 680px;
    font-size: 10px; font-weight: 400; color: var(--white);
  }
</style>
</head>
<body>
<section class="label">
  <svg class="label-art" width="358" height="703" viewBox="0 0 358 703">
    <defs>
      <linearGradient id="bg-blue" x1="0" y1="0" x2="1" y2="1">
        <stop offset="0" stop-color="#2a8ed0"/>
        <stop offset="0.5" stop-color="var(--brand-mid)"/>
        <stop offset="1" stop-color="var(--brand-deep)"/>
      </linearGradient>
      <linearGradient id="band" x1="0" y1="0" x2="1" y2="0">
        <stop offset="0" stop-color="#ffffff"/>
        <stop offset="0.3" stop-color="#1a8ad4"/>
        <stop offset="0.7" stop-color="#1a8ad4"/>
        <stop offset="1" stop-color="#ffffff"/>
      </linearGradient>
      <linearGradient id="photo" x1="0" y1="0" x2="1" y2="0">
        <stop offset="0" stop-color="#7d7e80"/>
        <stop offset="0.4" stop-color="#b9b9b8"/>
        <stop offset="0.6" stop-color="#eceff2"/>
        <stop offset="1" stop-color="#f7f8fa"/>
      </linearGradient>
      <radialGradient id="glow-left" cx="0.1" cy="0.9" r="0.35">
        <stop offset="0" stop-color="#ffffff" stop-opacity="0.95"/>
        <stop offset="1" stop-color="#ffffff" stop-opacity="0"/>
      </radialGradient>
      <radialGradient id="badge" cx="0.5" cy="0.6" r="0.6">
        <stop offset="0" stop-color="#ffffff"/>
        <stop offset="1" stop-color="#d9dde2"/>
      </radialGradient>
    </defs>
    <rect width="358" height="703" fill="url(#bg-blue)"/>
    <path d="M0 190 Q80 80 200 80 Q300 80 358 118 L358 243 L0 243 Z" fill="#00b7f1"/>
    <path d="M0 195 Q85 88 200 86 Q300 86 358 122 L358 243 L0 243 Z" fill="var(--white)"/>
    <rect x="0" y="242" width="358" height="46" fill="url(#band)"/>
    <rect x="0" y="288" width="358" height="260" fill="url(#photo)" role="img" aria-label="Photo of a clean modern bathroom with shower, vanity and bathtub"/>
    <path d="M0 494 Q60 540 140 548 Q260 550 358 430 L358 703 L0 703 Z" fill="#00b7f1"/>
    <path d="M0 498 Q60 545 140 553 Q260 556 358 438 L358 703 L0 703 Z" fill="url(#bg-blue)"/>
    <rect x="0" y="500" width="358" height="203" fill="url(#glow-left)"/>
    <rect x="160" y="550" width="118" height="19" fill="var(--brand-soft)" opacity="0.55"/>
    <g fill="none" stroke="var(--brand-pale)" stroke-width="2" opacity="0.8">
      <circle cx="41" cy="71" r="9"/>
      <circle cx="321" cy="108" r="14"/>
      <circle cx="330" cy="119" r="8"/>
      <circle cx="322" cy="526" r="9"/>
      <circle cx="38" cy="614" r="13"/>
      <circle cx="58" cy="634" r="7"/>
    </g>
    <circle cx="80" cy="522" r="52" fill="var(--brand-mid)"/>
    <circle cx="80" cy="522" r="49" fill="url(#badge)"/>
    <path d="M80 461 L102 469 Q104 495 80 507 Q56 495 58 469 Z" fill="var(--brand-mid)"/>
    <path d="M80 465 L99 472 Q100 493 80 503 Q60 493 61 472 Z" fill="var(--accent-yellow)"/>
    <path d="M69 482 L77 490 L92 475" fill="none" stroke="var(--brand-mid)" stroke-width="5" stroke-linecap="round" stroke-linejoin="round"/>
  </svg>

  <p class="tagline-small">A READY-TO-USE</p>
  <p class="tagline-main">PRODUCT FOR EVERYDAY USE.</p>
  <div class="brand-mark"></div>
  <p class="brand-name">vorlix</p>
  <p class="product-line">SANITARY</p>
  <p class="product-name">CLEANER</p>
  <p class="claim-badge">CLEANS,<br>DESCALES &amp;<br>FRESHENS</p>
  <p class="usage-heading">SUITABLE FOR</p>
  <ul class="usage-list">
    <li>BATHROOM</li>
    <li>SANITARY</li>
    <li>WET AREAS</li>
    <li>TOILET</li>
  </ul>
  <p class="benefit-intro">IDEAL FOR</p>
  <p class="benefit-main">QUICK AND POWERFUL CLEANING.</p>
  <p class="volume">500<small>ml</small></p>
  <p class="volume-unit">NET WT</p>
</section>
</body>
</html>
```